Maple Rug & Vent Cleaning

redesign of current website www.birchfreshrugwashing.net Looking for something similar to what we have but more professional and more user-friendly modern design for homepage and service page. A more professional looking contact form in the slider area of the homepage and a way to display 5 different phone number and regions above the fold, preferably the header.

Target Market(s)

Homeowners looking for top tier all-natural organic cleaning for their carpets, area rugs and air ducts.

Industry/Entity Type

Carpet

Number of Pages Required

2 page

Font styles to use
Sans Serif

Colors

Designer to choose colors to be used in the design.

Requirements
Must have
• A more professional looking contact form in the slider area of the homepage and a clear call to action
Nice to have
• a way to display 5 different phone numbers and regions above the fold, preferably the header.

```html
<!DOCTYPE html>
<html lang="en">
<head>
<meta charset="utf-8">
<title>Maple Rug &amp; Vent Cleaning – Homepage and Services</title>
<link href="https://fonts.googleapis.com/css2?family=Roboto:wght@400;500;700&display=swap" rel="stylesheet">
<style>
:root{
  --sky:#41a8f4;
  --green:#0aa84f;
  --green-dark:#078a40;
  --ink:#1e2328;
  --text:#555b61;
  --muted:#8a9096;
  --light:#f1f4f7;
  --footer:#1f262c;
  --yellow:#ffe81a;
  --white:#ffffff;
}
*{box-sizing:border-box;margin:0;padding:0}
html,body{width:960px;height:1200px;overflow:hidden}
body{background:var(--sky);font-family:"Roboto",Arial,sans-serif;color:var(--ink)}
.board{position:absolute;left:0;top:0;width:1725px;height:2156px;transform:scale(0.55652);transform-origin:0 0}
.page{position:absolute;background:var(--white);overflow:hidden}
.page-home{left:169px;top:130px;width:477px;height:1960px}
.page-services{left:745px;top:336px;width:828px;height:1820px}
.a{position:absolute}
.band-green{background:var(--green);color:var(--white)}
.band-light{background:var(--light)}
.band-dark{background:var(--footer);color:#c9ced3}
.photo{position:absolute}
.center{text-align:center}
.btn{position:absolute;display:flex;align-items:center;justify-content:center;font-weight:500}
.btn-green{background:var(--green);color:var(--white)}
.btn-dark{background:var(--ink);color:var(--white)}
.btn-outline{border:1px solid currentColor}
.label{color:var(--green);font-weight:500;letter-spacing:.5px;text-transform:uppercase}
.lorem{color:var(--text)}
.brand{font-weight:700;color:var(--green);letter-spacing:.5px;white-space:nowrap}
.stars{color:#f5a623;letter-spacing:1px}
.social{display:flex;gap:10px}
.social i{display:block;width:6px;height:6px;border-radius:50%;background:currentColor;opacity:.85}

/* services page */
.s-topbar{left:0;top:0;width:828px;height:33px;font-size:7.5px;display:flex;align-items:center;padding:0 62px;gap:16px}
.s-topbar .social{margin-left:auto}
.s-header{left:0;top:33px;width:828px;height:52px}
.s-nav{left:290px;top:57px;display:flex;gap:0;font-size:7.2px;color:var(--ink)}
.s-nav span{margin-right:16px}
.s-nav .on{color:var(--green)}
.s-hero-title{left:171px;top:172px;font-size:21px;font-weight:500;color:var(--white)}
.s-crumb{left:598px;top:181px;font-size:6px;color:var(--white)}
.card{position:absolute;width:151px;height:170px;background:var(--white);box-shadow:0 2px 8px rgba(0,0,0,.06);text-align:center}
.card .pic{position:absolute;left:0;top:0;width:151px;height:99px}
.card h3{position:absolute;top:113px;width:100%;font-size:8.5px;font-weight:500}
.card p{position:absolute;top:126px;left:8px;right:8px;font-size:5.6px;line-height:11px;color:var(--text)}
.card .rule{position:absolute;top:155px;left:67px;width:17px;height:1px;background:var(--sky)}
.step{position:absolute;width:140px;text-align:center}
.step .blob{margin:0 auto;width:66px;height:56px;background:var(--white);border-radius:48% 52% 40% 60%/55% 45% 55% 45%;box-shadow:0 4px 12px rgba(0,0,0,.05);display:flex;align-items:center;justify-content:center}
.num{position:absolute;width:14px;height:14px;border-radius:50%;background:var(--green);color:var(--white);font-size:6px;display:flex;align-items:center;justify-content:center}
.step h4{font-size:9.5px;font-weight:500;margin-top:38px}
.step p{font-size:5.6px;line-height:11px;color:var(--text);margin-top:4px}
.review{position:absolute;width:90px;text-align:center}
.review .count{font-size:5.5px;color:var(--text)}
.review .name{font-size:13px;font-weight:700;color:var(--ink);margin-top:4px}
.review .stars{font-size:7px}
.field{position:absolute;background:var(--white);font-size:5.5px;color:var(--muted);display:flex;align-items:center;padding-left:7px}
.foot-h{font-size:7.5px;color:var(--green)}
.foot-list{font-size:5.6px;line-height:13px}

/* homepage */
.h-topbar{left:0;top:0;width:477px;height:15px;font-size:3.6px;display:flex;align-items:center;padding:0 38px;gap:8px}
.h-topbar .social{margin-left:auto;gap:5px}
.h-topbar .social i{width:3px;height:3px}
.h-nav{left:170px;top:29px;display:flex;font-size:3.6px}
.h-nav span{margin-right:9px}
.tiny{font-size:3.4px;line-height:6px;color:var(--text)}
.mini-card{position:absolute;width:87px;height:98px;background:var(--white);text-align:center}
.mini-card .pic{height:57px}
.mini-card h5{font-size:4.3px;font-weight:500;margin-top:8px}
.mini-card p{font-size:3px;line-height:5px;color:var(--text);margin:2px 6px 0}
.region{font-size:5px;font-weight:700;line-height:7.5px;white-space:pre}
.member{position:absolute;width:60px;text-align:center}
.member .pic{width:48px;height:48px;margin:0 auto;border-radius:50%;background:#7a7a7a;border:3px solid #e6e6e6}
.member b{display:block;font-size:3.6px;color:var(--sky);margin-top:10px;font-weight:500}
.member span{display:block;font-size:3px;color:var(--text)}
.stat{position:absolute;width:70px;text-align:center;color:var(--white)}
.stat small{display:block;font-size:3px}
.stat strong{display:block;font-size:12px;font-weight:500;line-height:14px}
</style>
</head>
<body>
<svg width="0" height="0" style="position:absolute">
  <symbol id="tick" viewBox="0 0 12 12"><circle cx="6" cy="6" r="5.2" fill="none" stroke="currentColor" stroke-width="1.1"/><path d="M3.6 6.2l1.7 1.7 3.2-3.5" fill="none" stroke="currentColor" stroke-width="1.2"/></symbol>
  <symbol id="phone" viewBox="0 0 12 12"><path d="M3 1.5l2 2-1 1.2a7 7 0 003.3 3.3l1.2-1 2 2-1.3 1.5C5.6 10.2 1.8 6.4 1.5 2.8z" fill="currentColor"/></symbol>
  <symbol id="pin" viewBox="0 0 12 12"><path d="M6 1a3.5 3.5 0 013.5 3.5C9.5 7 6 11 6 11S2.5 7 2.5 4.5A3.5 3.5 0 016 1z" fill="currentColor"/><circle cx="6" cy="4.5" r="1.2" fill="#0aa84f"/></symbol>
  <symbol id="mail" viewBox="0 0 12 12"><rect x="1" y="2.5" width="10" height="7" fill="currentColor"/><path d="M1 2.5l5 4 5-4" fill="none" stroke="#0aa84f" stroke-width=".9"/></symbol>
  <symbol id="arrow-up" viewBox="0 0 12 12"><circle cx="6" cy="6" r="6" fill="#0aa84f"/><path d="M6 3v6M3.5 5.5L6 3l2.5 2.5" fill="none" stroke="#fff" stroke-width="1.2"/></symbol>
</svg>

<div class="board">

<!-- ================= HOMEPAGE ================= -->
<section class="page page-home">
  <div class="a h-topbar band-green">
    <span>Call Today Clean Today (555) 428-0100</span><span>Find us on Map</span><span>hello@maplerugvent.com</span>
    <span class="social"><i></i><i></i><i></i><i></i></span>
  </div>
  <div class="a brand" style="left:36px;top:22px;font-size:9px">MAPLE RUG</div>
  <nav class="a h-nav"><span style="color:var(--green)">Home</span><span>Why Maple Rug</span><span>Our Services +</span><span>Coupons</span><span>Gallary</span><span>Service Area</span><span>Contact</span></nav>
  <div class="btn btn-outline" style="left:378px;top:25px;width:40px;height:8px;font-size:3px;color:var(--green)">(555) 428-0100</div>
  <div class="btn btn-green" style="left:423px;top:25px;width:29px;height:8px;font-size:3px">Book Now</div>

  <div class="photo" role="img" aria-label="Technician cleaning a grey carpet with an extraction wand" style="left:0;top:45px;width:477px;height:178px;background:linear-gradient(100deg,#4d4d4f,#6f6e6c 45%,#3e3e40)"></div>
  <div class="a" style="left:100px;top:94px;font-size:3.6px;color:#ddd">✓ Trusted &nbsp; ✓ Simple &nbsp; ✓ Affordable</div>
  <h1 class="a" style="left:100px;top:103px;font-size:14.5px;line-height:17.5px;font-weight:500;color:var(--white)">20+ Years of Experience<br>in Carpet Cleaning<br>Service</h1>
  <div class="btn btn-green" style="left:100px;top:161px;width:47px;height:11px;font-size:3.4px">Book Now</div>
  <div class="btn btn-outline" style="left:152px;top:161px;width:46px;height:11px;font-size:3.4px;color:var(--white)">Our Services</div>
  <div class="a" style="left:20px;top:129px;width:9px;height:9px;border-radius:50%;background:#fff"></div>
  <div class="a" style="left:447px;top:129px;width:9px;height:9px;border-radius:50%;background:var(--green)"></div>
  <div class="a" style="left:320px;top:70px;width:81px;height:113px;background:#1f2326;border-top:2px solid var(--green)">
    <div class="label center" style="font-size:3.8px;margin-top:6px">Get a Free Quote</div>
    <div class="field" style="left:7px;top:18px;width:67px;height:9px;font-size:3px">Your Name</div>
    <div class="field" style="left:7px;top:34px;width:67px;height:9px;font-size:3px">Your Email</div>
    <div class="field" style="left:7px;top:50px;width:67px;height:9px;font-size:3px">Phone Number</div>
    <div class="field" style="left:7px;top:65px;width:67px;height:25px;font-size:3px;align-items:flex-start;padding-top:3px">Message</div>
    <div class="btn btn-green" style="left:7px;top:98px;width:67px;height:10px;font-size:3px">GET FREE QUOTE</div>
  </div>

  <div class="a band-green" style="left:0;top:223px;width:477px;height:32px">
    <div class="a" style="left:38px;top:6px;font-size:7px;line-height:9.5px;font-weight:500;color:var(--yellow);text-align:center">CALL FOR SERVICE<br>TO ALL CHICAGOLAND</div>
    <div class="a region" style="left:146px;top:5px">Chicago.................(555) 831-0190
Southwest Suburbs..........(555) 326-0120
South Suburbs..............(555) 390-0102</div>
    <div class="a region" style="left:298px;top:5px">North &amp; NW Suburbs.......(555) 428-0100
Near West Suburbs..........(555) 433-0176
DuPage County..............(555) 326-0120</div>
  </div>

  <div class="photo" role="img" aria-label="Gloved hand scrubbing a beige carpet" style="left:100px;top:280px;width:150px;height:125px;border-radius:48% 52% 45% 55%/50% 40% 60% 50%;background:radial-gradient(circle at 45% 45%,#e9d8b8,#c6a97f 60%,#9fc3d6)"></div>
  <div class="a" style="left:170px;top:330px;width:14px;height:14px;border-radius:50%;background:var(--sky)"></div>
  <div class="a label" style="left:262px;top:268px;font-size:3px">About us</div>
  <h2 class="a" style="left:262px;top:275px;font-size:11px;line-height:13.5px;font-weight:500">We are Different in<br>Carpet Cleaning<br>Industry</h2>
  <p class="a tiny" style="left:262px;top:318px;width:112px">Natural products, trained crews and honest pricing make every visit simple. We lift deep dirt, allergens and stains without harsh residue left behind.</p>
  <p class="a tiny" style="left:262px;top:342px;width:112px">Our family owned team has served local homes for years, with fast booking, careful work and a result you will notice the same day.</p>
  <div class="a tiny" style="left:262px;top:374px;color:var(--ink)">✓ Cost Effective &nbsp;&nbsp;&nbsp;&nbsp;&nbsp; ✓ Insured and Bonded<br>✓ 100% Satisfaction &nbsp;&nbsp; ✓ Quality Services</div>
  <div class="btn btn-green" style="left:262px;top:396px;width:47px;height:11px;font-size:3.4px">Read More</div>

  <div class="a band-light" style="left:0;top:433px;width:477px;height:307px"></div>
  <div class="a label" style="left:96px;top:443px;font-size:3px">Our services</div>
  <h2 class="a" style="left:96px;top:450px;font-size:10px;font-weight:500">Our Best Services For You</h2>
  <div class="mini-card" style="left:96px;top:472px"><div class="pic" role="img" aria-label="Carpet texture" style="background:#8a6a63"></div><h5>Carpet Cleaning</h5><p>Deep steam wash for every room of your home, done fast.</p></div>
  <div class="mini-card" style="left:191px;top:472px"><div class="pic" role="img" aria-label="Upholstery being cleaned" style="background:#d8d6cc"></div><h5 style="color:var(--green)">Upholstery Cleaning</h5><p>Gentle care for sofas and chairs of every fabric type.</p></div>
  <div class="mini-card" style="left:285px;top:472px"><div class="pic" role="img" aria-label="Open air duct" style="background:linear-gradient(#b9b4ac,#7f766d)"></div><h5>Air Duct Cleaning</h5><p>Clear dust from vents for cleaner air in every room.</p></div>
  <div class="mini-card" style="left:96px;top:594px"><div class="pic" role="img" aria-label="Patterned rug being washed" style="background:linear-gradient(120deg,#9b3b3a,#4a6f7e)"></div><h5>Oriental Rug Cleaning</h5><p>Hand care for wool and silk rugs with safe methods.</p></div>
  <div class="mini-card" style="left:191px;top:594px"><div class="pic" role="img" aria-label="Puppy lying on a carpet" style="background:#e8dccb"></div><h5>Pet Odor Removal</h5><p>Natural treatment that removes odor at the source.</p></div>
  <div class="mini-card" style="left:285px;top:594px"><div class="pic" role="img" aria-label="Water leaking from a ceiling" style="background:linear-gradient(#c8d9e2,#e07a3a)"></div><h5>Water Damage Restoration</h5><p>Quick drying and repair after leaks and floods.</p></div>
  <div class="a" style="left:101px;top:702px;font-size:4.5px;font-weight:500">And More Cleaning Solutions..</div>
  <div class="a tiny" style="left:101px;top:708px">Tile, grout and mattress care on request</div>
  <div class="btn btn-green" style="left:338px;top:703px;width:39px;height:10px;font-size:3px">View All</div>

  <div class="a band-green center" style="left:0;top:740px;width:477px;height:75px">
    <div style="font-size:10.5px;font-weight:500;margin-top:7px">CHICAGOLAND LEADER IN ECO-FRIENDLY CLEANING</div>
    <div style="font-size:4.2px;margin-top:8px">✓ Natural Cleaning &nbsp; ✓ Certified Technicians &nbsp; ✓ Stays Cleaner Longer &nbsp; ✓ Enviroment Safe</div>
    <div class="btn btn-outline" style="left:162px;top:52px;width:73px;height:16px;font-size:5.5px">(555) 428-0100</div>
    <div class="btn btn-dark" style="left:242px;top:52px;width:73px;height:16px;font-size:3.6px">Get a Quote Now</div>
  </div>

  <div class="a band-light" style="left:0;top:815px;width:477px;height:150px"></div>
  <div class="a label center" style="left:0;top:837px;width:477px;font-size:2.8px">How we work</div>
  <h2 class="a center" style="left:0;top:843px;width:477px;font-size:10px;font-weight:500">How <span style="color:var(--green)">‘Maple Rug’</span> Works</h2>
  <div class="a" style="left:144px;top:910px;width:190px;border-top:1px dotted var(--green)"></div>
  <div class="a" style="left:120px;top:866px;width:40px;height:30px;border-radius:50%;background:#fff"></div>
  <div class="a" style="left:215px;top:866px;width:40px;height:30px;border-radius:50%;background:#fff"></div>
  <div class="a" style="left:310px;top:866px;width:40px;height:30px;border-radius:50%;background:#fff"></div>
  <div class="num" style="left:139px;top:906px;width:9px;height:9px;font-size:3px">1</div>
  <div class="num" style="left:234px;top:906px;width:9px;height:9px;font-size:3px">2</div>
  <div class="num" style="left:329px;top:906px;width:9px;height:9px;font-size:3px">3</div>
  <div class="a center" style="left:104px;top:921px;width:80px;font-size:4.5px;font-weight:500">Book Online<div class="tiny" style="font-weight:400">Pick a time that suits<br>you in a few clicks</div></div>
  <div class="a center" style="left:199px;top:921px;width:80px;font-size:4.5px;font-weight:500">We Clean<div class="tiny" style="font-weight:400">Our crew arrives on<br>time and gets to work</div></div>
  <div class="a center" style="left:293px;top:921px;width:80px;font-size:4.5px;font-weight:500">You Relax<div class="tiny" style="font-weight:400">Enjoy a fresh home<br>with no extra effort</div></div>

  <div class="a label" style="left:76px;top:978px;font-size:2.8px">Why choose us</div>
  <h2 class="a" style="left:76px;top:983px;font-size:8.5px;line-height:9.5px;font-weight:500">Why use Maple Rug for all<br>your Rug &amp; Vent Cleaning<br>needs?</h2>
  <p class="a tiny" style="left:76px;top:1018px;width:136px;font-size:2.8px;line-height:4px">We offer a range of natural cleaning services and our skilled team is happy to answer any question you have. Call us today at (555) 428-0100 and we will be glad to help.</p>
  <div class="a tiny" style="left:76px;top:1044px;font-size:2.8px;line-height:14px;width:150px;color:var(--ink)">✓ Only green safe products &nbsp;&nbsp;&nbsp; ✓ Leading one year guarantee<br>✓ Over 20 years of cleaning &nbsp;&nbsp; ✓ Powerful modern equipment<br>✓ Non toxic detergents &nbsp;&nbsp;&nbsp;&nbsp;&nbsp;&nbsp;&nbsp; ✓ Certified trained technicians<br>✓ Safe for kids and pets &nbsp;&nbsp;&nbsp;&nbsp;&nbsp; ✓ Respect for your home</div>
  <div class="btn btn-green" style="left:76px;top:1100px;width:38px;height:9px;font-size:2.8px">Book Now</div>
  <div class="btn btn-outline" style="left:120px;top:1100px;width:38px;height:9px;font-size:2.8px;color:var(--sky)">Services</div>
  <div class="photo" role="img" aria-label="Family lying together on a clean carpet" style="left:220px;top:988px;width:155px;height:115px;border-radius:45% 55% 50% 50%/45% 50% 50% 55%;background:radial-gradient(circle at 45% 55%,#f2cf8c,#d5b796 55%,#eee6dd)"></div>
  <div class="a" style="left:134px;top:1128px;font-size:4px;font-weight:500">Frequently asked questions</div>
  <div class="a tiny" style="left:134px;top:1138px;width:209px;height:10px;background:var(--light);padding:2px 6px">What cleaning supplies do I have to provide? <span style="float:right;color:var(--sky)">+</span></div>
  <div class="a tiny" style="left:134px;top:1156px;width:209px;height:10px;border:1px solid var(--green);padding:2px 6px;color:var(--green)">Are the cleaners insured in case of damages? <span style="float:right">+</span></div>
  <div class="a tiny" style="left:134px;top:1174px;width:209px;height:10px;background:var(--light);padding:2px 6px">How soon can a crew come out to my home? <span style="float:right;color:var(--sky)">+</span></div>

  <div class="a band-light" style="left:0;top:1205px;width:477px;height:155px"></div>
  <div class="a label" style="left:100px;top:1227px;font-size:2.8px">Our team</div>
  <h2 class="a" style="left:100px;top:1233px;font-size:10px;font-weight:500">Experienced Team</h2>
  <div class="a" style="left:354px;top:1236px;width:8px;height:8px;border-radius:50%;border:1px solid #ccc"></div>
  <div class="a" style="left:367px;top:1236px;width:8px;height:8px;border-radius:50%;background:var(--sky)"></div>
  <div class="member" style="left:102px;top:1258px" role="img" aria-label="Team member portrait"><div class="pic"></div><b>Mara Lin</b><span>Office Cleaning Specialist</span></div>
  <div class="member" style="left:173px;top:1258px" role="img" aria-label="Team member portrait"><div class="pic"></div><b>Owen Hale</b><span>Office Cleaning Specialist</span></div>
  <div class="member" style="left:244px;top:1258px" role="img" aria-label="Team member portrait"><div class="pic" style="background:var(--sky)"></div><b>Ana Ruiz</b><span>Office Cleaning Specialist</span></div>
  <div class="member" style="left:315px;top:1258px" role="img" aria-label="Team member portrait"><div class="pic"></div><b>Theo</b><span>Office Cleaning Specialist</span></div>

  <div class="photo" role="img" aria-label="Gloved hand cleaning a carpet" style="left:0;top:1360px;width:477px;height:90px;background:linear-gradient(90deg,#6b6560,#9d8f7d 60%,#c8b27a)"></div>
  <h2 class="a" style="left:100px;top:1380px;font-size:10px;font-weight:500;color:#fff">We Have Our Own Style</h2>
  <p class="a tiny" style="left:100px;top:1395px;width:140px;color:#eee;font-size:2.8px;line-height:4px">A fresh approach to deep cleaning that keeps your floors looking new for longer.</p>
  <div class="btn btn-green" style="left:100px;top:1416px;width:47px;height:9px;font-size:2.8px">Book Now</div>
  <div class="a" style="left:344px;top:1393px;width:20px;height:20px;border-radius:50%;background:var(--green)"></div>

  <div class="a label center" style="left:0;top:1470px;width:477px;font-size:2.8px">Testimonials</div>
  <h2 class="a center" style="left:0;top:1478px;width:477px;font-size:10px;font-weight:500">What Our Clients Say?</h2>
  <div class="a" style="left:231px;top:1500px;width:18px;height:18px;border-radius:50%;background:#888" role="img" aria-label="Client portrait"></div>
  <p class="a center" style="left:110px;top:1524px;width:257px;font-size:4.5px;line-height:7.5px;font-style:italic;color:var(--text)">"Excellent job! My house has never been so clean! They showed up on time, worked carefully and were very courteous. We will definitely be having them come back again!"</p>
  <div class="a center stars" style="left:0;top:1550px;width:477px;font-size:3.5px">★★★★★</div>
  <div class="a center" style="left:0;top:1556px;width:477px;font-size:3px;color:var(--sky)">Nora <span style="color:var(--muted)">CEO, Bay Company</span></div>
  <div class="a center" style="left:100px;top:1600px;width:60px;font-size:5px;font-weight:700"><div style="font-size:2.6px;font-weight:400">60 Reviews</div>RateHub<div class="stars" style="font-size:3px">★★★★★</div></div>
  <div class="a center" style="left:180px;top:1600px;width:60px;font-size:5px;font-weight:700"><div style="font-size:2.6px;font-weight:400">120 Reviews</div>SearchRate<div class="stars" style="font-size:3px">★★★★★</div></div>
  <div class="a center" style="left:250px;top:1600px;width:60px;font-size:5px;font-weight:700"><div style="font-size:2.6px;font-weight:400">300 Reviews</div>SocialBook<div class="stars" style="font-size:3px">★★★★★</div></div>
  <div class="a center" style="left:320px;top:1600px;width:60px;font-size:5px;font-weight:700"><div style="font-size:2.6px;font-weight:400">90 Reviews</div>LocalStars<div class="stars" style="font-size:3px">★★★★★</div></div>

  <div class="a label center" style="left:0;top:1647px;width:477px;font-size:2.8px">Our portfolio</div>
  <h2 class="a center" style="left:0;top:1653px;width:477px;font-size:10px;font-weight:500">Our Latest Works</h2>
  <div class="photo" role="img" aria-label="Gloved hand cleaning carpet" style="left:0;top:1675px;width:95px;height:108px;background:linear-gradient(#f0e6d8,#d9b36a)"></div>
  <div class="photo" role="img" aria-label="Carpet cleaning wand on carpet" style="left:95px;top:1675px;width:96px;height:108px;background:linear-gradient(#a29a91,#c8b9a2)"></div>
  <div class="photo" role="img" aria-label="Office cleaning project" style="left:191px;top:1675px;width:96px;height:108px;background:#5fbf85"></div>
  <div class="a center" style="left:191px;top:1713px;width:96px;font-size:4px;color:#fff">Office Cleaning<div class="btn" style="position:relative;margin:6px auto 0;width:28px;height:7px;background:#1f262c;font-size:2.5px">VIEW PROJECT</div></div>
  <div class="photo" role="img" aria-label="Gloved hand cleaning carpet" style="left:287px;top:1675px;width:95px;height:108px;background:linear-gradient(#f0e6d8,#d9b36a)"></div>
  <div class="photo" role="img" aria-label="Technician vacuuming carpet" style="left:382px;top:1675px;width:95px;height:108px;background:linear-gradient(#6d7178,#b9b3aa)"></div>
  <div class="a band-green" style="left:0;top:1783px;width:477px;height:54px">
    <div class="stat" style="left:98px;top:4px"><small>More than</small><strong>8000+</strong><small>Clients</small></div>
    <div class="stat" style="left:168px;top:4px"><small>Over</small><strong>10000+</strong><small>Satisfied Clients</small></div>
    <div class="stat" style="left:239px;top:4px"><small>Over</small><strong>200+</strong><small>Professionals</small></div>
    <div class="stat" style="left:309px;top:4px"><small>More than</small><strong>25+</strong><small>Years of Experience</small></div>
  </div>
  <footer class="a band-dark" style="left:0;top:1837px;width:477px;height:123px">
    <div class="a brand" style="left:100px;top:13px;font-size:9px">MAPLE RUG</div>
    <p class="a tiny" style="left:100px;top:38px;width:80px;color:#aab;font-size:2.8px;line-height:4.5px">Natural cleaning for carpets, rugs and air ducts across the area since day one.</p>
    <div class="a" style="left:100px;top:63px;font-size:2.8px;color:var(--green);line-height:6px">hello@maplerugvent.com<br>(555) 428-0100</div>
    <div class="a" style="left:203px;top:15px;font-size:3px;color:var(--green)">Quick Links<div class="tiny" style="color:#ccc;font-size:2.6px;line-height:5px;margin-top:4px">Why Maple Rug?<br>Our Services<br>Coupons<br>Service Area<br>Gallery<br>Contact Us</div></div>
    <div class="a" style="left:266px;top:15px;font-size:3px;color:var(--green)">Our Services<div class="tiny" style="color:#ccc;font-size:2.6px;line-height:5px;margin-top:4px">Carpet Cleaning<br>Air Duct Cleaning<br>Pet Odor Removal<br>Oriental Rug Cleaning<br>Upholstery Cleaning<br>Tile &amp; Grout Cleaning<br>Water Dmage Restoration<br>Mattress Cleaning</div></div>
    <div class="btn btn-green" style="left:336px;top:15px;width:42px;height:9px;font-size:2.6px">Book Now</div>
    <div class="btn btn-outline" style="left:336px;top:29px;width:42px;height:9px;font-size:2.6px;color:#ccc">Join Us</div>
    <div class="btn btn-outline" style="left:336px;top:44px;width:42px;height:9px;font-size:2.6px;color:#ccc">Newsletter</div>
    <div class="a social" style="left:342px;top:79px;gap:5px"><i style="width:3px;height:3px"></i><i style="width:3px;height:3px"></i><i style="width:3px;height:3px"></i><i style="width:3px;height:3px"></i></div>
    <div class="a" style="left:100px;top:112px;font-size:2.8px">© MapleRug 2020 Allright Reserved</div>
    <svg class="a" style="left:370px;top:109px" width="8" height="8"><use href="#arrow-up"/></svg>
  </footer>
</section>

<!-- ================= SERVICES PAGE ================= -->
<section class="page page-services">
  <div class="a s-topbar band-green">
    <span>Call Today Clean Today (555) 428-0100</span>
    <span><svg width="7" height="7" style="vertical-align:-1px"><use href="#pin" fill="#fff"/></svg> Find us on Map</span>
    <span><svg width="7" height="7" style="vertical-align:-1px;color:#fff"><use href="#mail"/></svg> hello@maplerugvent.com</span>
    <span class="social"><i></i><i></i><i></i><i></i></span>
  </div>
  <header class="a s-header">
    <div class="a brand" style="left:58px;top:14px;font-size:18px">MAPLE RUG</div>
  </header>
  <nav class="a s-nav"><span class="on">Home</span><span>Why Maple Rug</span><span>Our Services +</span><span>Coupons</span><span>Gallary</span><span>Service Area</span><span>Contact</span></nav>
  <div class="btn btn-outline" style="left:652px;top:48px;width:69px;height:17px;font-size:6px;color:var(--green);gap:2px"><svg width="6" height="6"><use href="#phone"/></svg>(555) 428-0100</div>
  <div class="btn btn-green" style="left:731px;top:48px;width:49px;height:17px;font-size:6.5px">Book Now</div>

  <div class="photo" role="img" aria-label="Gloved hand cleaning a beige carpet" style="left:0;top:85px;width:828px;height:162px;background:linear-gradient(100deg,#6b5f52,#a08c6e 45%,#7d6d5b 75%,#5d5247)"></div>
  <h1 class="a s-hero-title">Our Services</h1>
  <div class="a s-crumb">Home &nbsp;/&nbsp; Services</div>

  <article class="card" style="left:171px;top:296px"><div class="pic" role="img" aria-label="Close up of carpet fibers" style="background:linear-gradient(135deg,#96766d,#7b5e57)"></div><h3>Carpet Cleaning</h3><p>Lorem ipsum dolor sit amet consectetur adi pisicing elit, sed do eiusmod tempor</p><div class="rule"></div></article>
  <article class="card" style="left:335px;top:296px"><div class="pic" role="img" aria-label="Upholstery cleaning tool on a mattress" style="background:linear-gradient(135deg,#e3e1d8,#c6c3b8)"></div><h3 style="color:var(--green)">Upholstery Cleaning</h3><p>Lorem ipsum dolor sit amet consectetur adi pisicing elit, sed do eiusmod tempor</p><div class="rule"></div></article>
  <article class="card" style="left:498px;top:296px"><div class="pic" role="img" aria-label="Inside of a dusty air duct" style="background:linear-gradient(#c9c5be,#8e857b 60%,#6e655c)"></div><h3>Air Duct Cleaning</h3><p>Lorem ipsum dolor sit amet consectetur adi pisicing elit, sed do eiusmod tempor</p><div class="rule"></div></article>
  <article class="card" style="left:171px;top:507px"><div class="pic" role="img" aria-label="Oriental rug being washed" style="background:linear-gradient(135deg,#a13c3a,#6e3a44 50%,#4f8a8f)"></div><h3>Oriental Rug Cleaning</h3><p>Lorem ipsum dolor sit amet consectetur adi pisicing elit, sed do eiusmod tempor</p><div class="rule"></div></article>
  <article class="card" style="left:335px;top:507px"><div class="pic" role="img" aria-label="Puppy lying on a stained carpet" style="background:linear-gradient(135deg,#f0e7da,#d9c8b2)"></div><h3>Pet Odor Removal</h3><p>Lorem ipsum dolor sit amet consectetur adi pisicing elit, sed do eiusmod tempor</p><div class="rule"></div></article>
  <article class="card" style="left:498px;top:507px"><div class="pic" role="img" aria-label="Water leaking from a ceiling into a bowl" style="background:linear-gradient(#a8c4d2,#d9e3e8 45%,#e07a3a)"></div><h3>Water Damage Restoration</h3><p>Lorem ipsum dolor sit amet consectetur adi pisicing elit, sed do eiusmod tempor</p><div class="rule"></div></article>

  <section class="a band-light" style="left:0;top:711px;width:828px;height:259px">
    <div class="a label center" style="left:0;top:35px;width:828px;font-size:5.5px">········ How we work ········</div>
    <h2 class="a center" style="left:0;top:48px;width:828px;font-size:21px;font-weight:500">How <span style="color:var(--green)">‘Maple Rug’</span> Works</h2>
    <div class="a" style="left:244px;top:166px;width:329px;border-top:1px dotted var(--green)"></div>
    <div class="num" style="left:237px;top:159px">1</div>
    <div class="num" style="left:402px;top:159px">2</div>
    <div class="num" style="left:565px;top:159px">3</div>
    <div class="step" style="left:174px;top:84px">
      <div class="blob"><svg width="30" height="26" viewBox="0 0 30 26" fill="none" stroke="#41a8f4" stroke-width="1.3"><rect x="5" y="3" width="20" height="14" rx="1"/><path d="M2 20h26l-2 3H4z"/><path d="M11 10l3 3 5-6"/></svg></div>
      <h4>Book Online</h4><p>Lorem ipsum dolor sit amet co<br>nsectetur adipisicing elitsed</p>
    </div>
    <div class="step" style="left:339px;top:84px">
      <div class="blob"><svg width="30" height="30" viewBox="0 0 30 30" fill="none" stroke="#41a8f4" stroke-width="1.3"><path d="M8 6l12 12"/><path d="M18 16l-4 4 6 6 4-4z"/><circle cx="6" cy="14" r="1"/><circle cx="11" cy="21" r="1"/><circle cx="20" cy="6" r="1"/></svg></div>
      <h4>We Clean</h4><p>Lorem ipsum dolor sit amet co<br>nsectetur adipisicing elitsed</p>
    </div>
    <div class="step" style="left:502px;top:84px">
      <div class="blob"><svg width="32" height="28" viewBox="0 0 32 28" fill="none" stroke="#41a8f4" stroke-width="1.3"><rect x="4" y="8" width="18" height="12" rx="2"/><path d="M4 14h18M6 20v4M20 20v4"/><path d="M26 4v20M24 4h4"/></svg></div>
      <h4>You Relax</h4><p>Lorem ipsum dolor sit amet co<br>nsectetur adipisicing elitsed</p>
    </div>
  </section>

  <section class="a band-green center" style="left:0;top:970px;width:824px;height:144px">
    <h2 style="font-size:26px;font-weight:500;margin-top:13px">CHICAGOLAND LEADER IN ECO-FRIENDLY CLEANING</h2>
    <div style="font-size:11px;margin-top:16px;display:flex;justify-content:center;gap:12px">
      <span><svg width="11" height="11" style="vertical-align:-1px"><use href="#tick"/></svg> Natural Cleaning</span>
      <span><svg width="11" height="11" style="vertical-align:-1px"><use href="#tick"/></svg> Certified Technicians</span>
      <span><svg width="11" height="11" style="vertical-align:-1px"><use href="#tick"/></svg> Stays Cleaner Longer</span>
      <span><svg width="11" height="11" style="vertical-align:-1px"><use href="#tick"/></svg> Enviroment Safe</span>
    </div>
    <div class="btn btn-outline" style="left:277px;top:96px;width:126px;height:30px;font-size:13px;border-radius:2px">(555) 428-0100</div>
    <div class="btn btn-dark" style="left:416px;top:95px;width:126px;height:31px;font-size:8.5px;border-radius:2px">Get a Quote Now</div>
  </section>

  <div class="a label center" style="left:0;top:1161px;width:828px;font-size:5.5px">········ Testimonials ········</div>
  <h2 class="a center" style="left:0;top:1173px;width:828px;font-size:20px;font-weight:500">What Our Clients Say?</h2>
  <div class="photo" role="img" aria-label="Smiling family lying on a clean carpet" style="left:203px;top:1212px;width:191px;height:157px;background:linear-gradient(135deg,#e7ddd2,#d9b37e 50%,#c9b9a8)"></div>
  <div class="a" style="left:394px;top:1212px;width:206px;height:157px;background:var(--footer);color:#fff;padding:18px 20px">
    <div class="stars" style="font-size:7px">★★★★★</div>
    <div style="font-size:8px;font-weight:500;margin-top:7px">They're Exactly What I Had in Mind</div>
    <p style="font-size:5.7px;line-height:11.5px;color:#c8cdd2;margin-top:7px">Duis aute irure dolor in reprehenderit in voluptate velit esse cillum dolore eu fugiat nulla pariatur. eaque ipsa quae incididunt ut labore et dolore magna aliqua nulla pariatu cillum dolore at nulla pariatur at nulla pariatur. cillum dolore eu fugiat nulla pariatur.</p>
    <div style="font-size:7px;font-weight:500;margin-top:7px">Daniel Reed</div>
    <div style="font-size:5px;color:#c8cdd2;margin-top:2px">Resident in Chicago area</div>
    <div class="a" style="left:145px;top:127px;width:10px;height:10px;border-radius:50%;border:1px solid var(--green)"></div>
    <div class="a" style="left:164px;top:127px;width:10px;height:10px;border-radius:50%;border:1px solid var(--green)"></div>
  </div>
  <div class="review" style="left:195px;top:1401px"><div class="count">60 Reviews</div><div class="name">RateHub</div><div class="stars">★★★★★</div></div>
  <div class="review" style="left:312px;top:1401px"><div class="count">120 Reviews</div><div class="name">SearchRate</div><div class="stars">★★★★★</div></div>
  <div class="review" style="left:421px;top:1401px"><div class="count">300 Reviews</div><div class="name">SocialBook</div><div class="stars">★★★★★</div></div>
  <div class="review" style="left:533px;top:1401px"><div class="count">90 Reviews</div><div class="name">LocalStars</div><div class="stars">★★★★★</div></div>

  <section class="a band-green" style="left:0;top:1467px;width:828px;height:85px">
    <h2 class="a center" style="left:0;top:8px;width:828px;font-size:19px;font-weight:500">Get a Free Call Back!</h2>
    <div class="field" style="left:219px;top:48px;width:145px;height:21px">Your name</div>
    <div class="field" style="left:379px;top:48px;width:140px;height:21px">Your phone numner</div>
    <div class="btn btn-dark" style="left:528px;top:47px;width:80px;height:22px;font-size:6.5px">Send Now</div>
  </section>

  <footer class="a band-dark" style="left:0;top:1552px;width:828px;height:220px">
    <div class="a brand" style="left:173px;top:28px;font-size:18px">MAPLE RUG</div>
    <p class="a" style="left:173px;top:70px;width:140px;font-size:6px;line-height:13px">Lorem ipsum dolor sit amet consectetur adipi sicing elit, sed do eiusmod tempor incididunt ut labore et dolore magna aliqua dolor.</p>
    <div class="a" style="left:173px;top:119px;font-size:6.3px;line-height:16px;color:var(--green)">hello@maplerugvent.com<br>(555) 428-0100</div>
    <div class="a foot-h" style="left:352px;top:38px">Quick Links</div>
    <div class="a" style="left:352px;top:51px;width:14px;height:1px;background:var(--green)"></div>
    <div class="a foot-list" style="left:352px;top:63px">Why MapleRug?<br>Our Services<br>Coupons<br>Service Area<br>Gallery<br>Contact Us</div>
    <div class="a foot-h" style="left:461px;top:38px">Our Services</div>
    <div class="a" style="left:461px;top:51px;width:14px;height:1px;background:var(--green)"></div>
    <div class="a foot-list" style="left:461px;top:63px">Carpet Cleaning<br>Air Duct CLeaning<br>Pet Odor Removal<br>Oriental Rug Cleaning<br>Upholstery Cleaning<br>Tile &amp; Grout Cleaning<br>Water Dmage Restoration<br>Mattres Cleaning</div>
    <div class="btn btn-green" style="left:581px;top:40px;width:72px;height:19px;font-size:5.8px">Book Now</div>
    <div class="btn btn-outline" style="left:581px;top:67px;width:72px;height:19px;font-size:5.8px;color:#d5dade">Join Us</div>
    <div class="btn btn-outline" style="left:581px;top:94px;width:72px;height:19px;font-size:5.8px;color:#d5dade">Newsletter</div>
    <div class="a social" style="left:589px;top:134px;gap:11px"><i></i><i></i><i></i><i></i></div>
    <div class="a" style="left:173px;top:180px;width:481px;height:1px;background:#3a434b"></div>
    <div class="a" style="left:173px;top:196px;font-size:5.8px">© MapleRug 2020 Allright Reserved</div>
    <svg class="a" style="left:640px;top:194px" width="13" height="13"><use href="#arrow-up"/></svg>
  </footer>
</section>

</div>
</body>
</html>
```